Business card for medical clinic

I need an upmarket, modern medical/health business card for my clinic

Contact Information for Business Card

name, address, email, qr code

```html
<!DOCTYPE html>
<html lang="en">
<head>
<meta charset="utf-8">
<title>Meridian Care Clinic – Business Card</title>
<link rel="stylesheet" href="https://fonts.googleapis.com/css2?family=Cinzel:wght@600&family=Arimo:wght@400&display=swap">
<style>
  :root {
    --backdrop: #d3d3d3;
    --card: #ffffff;
    --navy: #1c3a66;
    --brand-blue: #1a5c96;
    --sky: #27a4df;
    --ink: #2a2a2a;
    --shadow: rgba(0, 0, 0, 0.22);
  }
  * { box-sizing: border-box; margin: 0; padding: 0; }
  html, body {
    width: 1200px; height: 915px; overflow: hidden;
    background: var(--backdrop);
  }
  .canvas {
    position: relative; width: 1200px; height: 915px;
    display: flex; flex-direction: column; align-items: center;
    justify-content: center; gap: 48px;
  }
  .card {
    position: relative; width: 600px; height: 343px;
    background: var(--card); border-radius: 22px;
    box-shadow: 0 6px 16px var(--shadow);
    overflow: hidden;
  }
  .brand {
    display: flex; align-items: center; gap: 14px;
  }
  .brand-dot {
    width: 34px; height: 34px; border-radius: 50%;
    border: 4px solid var(--brand-blue); flex: none;
  }
  .brand-name {
    font-family: "Cinzel", serif; font-weight: 600;
    color: var(--brand-blue); letter-spacing: 1px; white-space: nowrap;
  }

  /* Front */
  .card-front { display: flex; align-items: center; justify-content: center; }
  .card-front .brand-name { font-size: 34px; }

  /* Back */
  .card-back .brand { position: absolute; left: 40px; top: 52px; }
  .card-back .brand-dot { width: 26px; height: 26px; border-width: 3px; }
  .card-back .brand-name { font-size: 22px; }

  .contact {
    position: absolute; left: 42px; top: 160px;
    font-family: "Arimo", sans-serif; color: var(--ink);
    font-size: 15px; line-height: 1.3;
  }
  .address { margin-bottom: 14px; }
  .contact-list { list-style: none; }
  .contact-list li { display: flex; align-items: center; gap: 9px; margin-bottom: 4px; }
  .contact-list svg { width: 13px; height: 13px; flex: none; }

  .person {
    position: absolute; right: 40px; top: 118px; text-align: right;
  }
  .person-name {
    font-family: "Cinzel", serif; font-weight: 600; font-size: 24px;
    color: var(--brand-blue); letter-spacing: 1px;
  }
  .person-role {
    font-family: "Arimo", sans-serif; font-size: 15px; color: var(--ink);
  }
  .accent-tab {
    position: absolute; right: 0; top: 92px; width: 22px; height: 28px;
    background: linear-gradient(160deg, var(--navy), var(--sky));
  }
</style>
</head>
<body>
<main class="canvas">
  <section class="card card-front" aria-label="Card front">
    <div class="brand">
      <span class="brand-dot"></span>
      <span class="brand-name">Meridian Care Clinic</span>
    </div>
  </section>

  <section class="card card-back" aria-label="Card back">
    <div class="brand">
      <span class="brand-dot"></span>
      <span class="brand-name">Meridian Care Clinic</span>
    </div>

    <div class="accent-tab"></div>
    <div class="person">
      <p class="person-name">Daniel Hale</p>
      <p class="person-role">Director/Founder</p>
    </div>

    <div class="contact">
      <p class="address">2187 Harbor Lane<br>Westfield CA 90412</p>
      <ul class="contact-list">
        <li>
          <svg viewBox="0 0 16 16" aria-hidden="true"><path fill="#27a4df" d="M3.5 1.5l2.5 3-1.5 1.8c.8 1.8 2.4 3.4 4.2 4.2l1.8-1.5 3 2.5-1.6 2.3C6.5 13.5 2.5 9.5 1.2 3.1z"/></svg>
          05318 472 6690
        </li>
        <li>
          <svg viewBox="0 0 16 16" aria-hidden="true"><rect x="1" y="3" width="14" height="10" rx="1.5" fill="#27a4df"/><path d="M1.5 4l6.5 5 6.5-5" stroke="#fff" stroke-width="1.3" fill="none"/></svg>
          info@meridiancareclinic.com
        </li>
        <li>
          <svg viewBox="0 0 16 16" aria-hidden="true"><circle cx="8" cy="8" r="7" fill="#27a4df"/><path d="M1 8h14M8 1c-3 3.5-3 10.5 0 14M8 1c3 3.5 3 10.5 0 14" stroke="#fff" stroke-width="1.1" fill="none"/></svg>
          www.meridiancareclinic.com
        </li>
      </ul>
    </div>
  </section>
</main>
</body>
</html>
```